ReelBloom business card

We are a performing arts company providing training (to both kids and adults) as well as performers for events. We hope to bring joy and confidence on stage to the people we train, as well as joy to the audience when our artistes perform. Designs should convey the joy, confidence and vibrancy on stage. Design business card using the attached logo. Card to include name, mobile tel, email address, company address, and website. Double sided. To also include the following list of what the company does:
• Training & Enrichment
• Private & Corporate Entertainment
- Music composition & production

Industry/Entity Type

Training

Contact Information for Business Card

Card to include name, mobile tel, email address, company address, and website. Double sided. To also include the following list of what the company does:
• Training & Enrichment

Requirements
Nice to have
• Card need not be the traditional rectangular in shape but not too outrageous.

```html
<!DOCTYPE html>
<html lang="en">
<head>
<meta charset="UTF-8">
<title>ReelBloom Business Card</title>
<link rel="stylesheet" href="https://fonts.googleapis.com/css2?family=Ubuntu:wght@400;500;700&display=swap">
<style>
  :root {
    --page-bg: #d9dad6;
    --card-white: #ffffff;
    --brand-red: #e31b23;
    --brand-red-dark: #b8151b;
    --panel-top: #8f928a;
    --panel-bottom: #9aab74;
    --ink: #1b1b1b;
    --brand-ink: #35307a;
  }
  * { margin: 0; padding: 0; box-sizing: border-box; }
  html, body {
    width: 1200px;
    height: 902px;
    overflow: hidden;
    background: var(--page-bg);
    font-family: "Ubuntu", sans-serif;
  }
  .card {
    position: absolute;
    left: 110px;
    top: 170px;
    width: 980px;
    height: 562px;
    border-radius: 18px;
    overflow: hidden;
    background: var(--card-white);
    box-shadow: 0 10px 30px rgba(0,0,0,0.18);
  }
  .card-art {
    position: absolute;
    inset: 0;
    width: 980px;
    height: 562px;
  }
  .brand {
    position: absolute;
    left: 0;
    width: 442px;
    top: 150px;
    text-align: center;
  }
  .brand-mark {
    display: block;
    width: 110px;
    height: 110px;
    margin: 0 auto 20px;
    border-radius: 50%;
    background: var(--brand-red);
  }
  .brand-name {
    font-size: 66px;
    font-weight: 500;
    color: var(--brand-ink);
    letter-spacing: 0.5px;
  }
  .details {
    position: absolute;
    left: 553px;
    top: 88px;
    color: var(--ink);
  }
  .person-name {
    font-size: 33px;
    font-weight: 500;
    color: var(--brand-red);
    line-height: 38px;
  }
  .person-title {
    font-size: 24px;
    line-height: 28px;
    margin-bottom: 40px;
  }
  .address {
    font-size: 22px;
    line-height: 28px;
    margin-bottom: 30px;
  }
  .contact-list { list-style: none; margin-bottom: 30px; }
  .contact-list li {
    display: flex;
    align-items: center;
    font-size: 22px;
    line-height: 29px;
  }
  .contact-icon {
    width: 18px;
    height: 18px;
    margin: 0 18px 0 9px;
    flex: none;
  }
  .services { list-style: none; }
  .services li {
    font-size: 22px;
    line-height: 28.5px;
  }
</style>
</head>
<body>
  <div class="card">
    <svg class="card-art" viewBox="0 0 980 562" aria-hidden="true">
      <defs>
        <linearGradient id="panelFill" x1="0" y1="0" x2="0.4" y2="1">
          <stop offset="0" stop-color="var(--panel-top)"/>
          <stop offset="1" stop-color="var(--panel-bottom)"/>
        </linearGradient>
        <linearGradient id="bandFill" x1="0" y1="0" x2="1" y2="1">
          <stop offset="0" stop-color="var(--brand-red)"/>
          <stop offset="1" stop-color="var(--brand-red-dark)"/>
        </linearGradient>
      </defs>
      <path class="panel" d="M0 0 H388 C470 120 480 400 397 562 H0 Z" fill="url(#panelFill)"/>
      <path class="band" d="M388 0 H445 C505 150 505 420 410 562 H397 C480 400 470 120 388 0 Z" fill="url(#bandFill)"/>
    </svg>

    <div class="brand">
      <span class="brand-mark"></span>
      <div class="brand-name">ReelBloom</div>
    </div>

    <div class="details">
      <div class="person-name">Employee Name</div>
      <div class="person-title">Your Title</div>
      <div class="address">Your Adress Inc 2nd Lane<br>Ave Edison, NJ 00000</div>
      <ul class="contact-list">
        <li>
          <svg class="contact-icon" viewBox="0 0 18 18"><rect width="18" height="18" rx="2" fill="var(--brand-red)"/><rect x="5" y="3" width="8" height="12" rx="1" fill="#fff"/><rect x="6.5" y="5" width="5" height="6" fill="var(--brand-red)"/></svg>
          0012 3456 789
        </li>
        <li>
          <svg class="contact-icon" viewBox="0 0 18 18"><rect width="18" height="18" rx="2" fill="var(--brand-red)"/><rect x="3" y="5" width="12" height="8" fill="#fff"/><path d="M3 5 L9 10 L15 5" stroke="var(--brand-red)" stroke-width="1.4" fill="none"/></svg>
          info@youremail.com
        </li>
        <li>
          <svg class="contact-icon" viewBox="0 0 18 18"><rect width="18" height="18" rx="2" fill="var(--brand-red)"/><circle cx="9" cy="9" r="5.5" fill="none" stroke="#fff" stroke-width="1.5"/><path d="M3.5 9 H14.5 M9 3.5 V14.5" stroke="#fff" stroke-width="1.2"/></svg>
          www.yourwebsite.com
        </li>
      </ul>
      <ul class="services">
        <li>Training &amp; Enrichment</li>
        <li>Private &amp; Corporate Entertainment</li>
        <li>Music composition &amp; production</li>
      </ul>
    </div>
  </div>
</body>
</html>
```